Business card for law firm

Need business card for new law firm. Think confident, authoritative, conservative, but not stuffy or old-fashioned.

Contact Information for Business Card

Content for card - logo (uploaded), plus the following:

Paul Whitcombe (larger font)
Managing Partner (larger font, but not as large as name)
Level 9, 7 Ferris Lane
Sydney NSW 2000
Main Tel 02 9364 2710
Direct Tel 02 8472 3159
Email paul@qvlegal.com.au
www.qvlegal.com.au

Letterhead design should include logo plus:
Level 9, 7 Ferris Lane
Sydney NSW 2000
Tel 02 8472 3159
www.qvlegal.com.au

```html
<!DOCTYPE html>
<html lang="en">
<head>
<meta charset="utf-8">
<title>Quayvale Lawyers – Business Card</title>
<link rel="stylesheet" href="https://fonts.googleapis.com/css2?family=Arimo:wght@700&family=Roboto:wght@400&display=swap">
<style>
  :root {
    --navy: #0a1170;
    --ink: #111111;
    --text: #2a2a2a;
    --rule: #8a8d8c;
    --paper: #ffffff;
  }
  * { margin: 0; padding: 0; box-sizing: border-box; }
  html, body { width: 1200px; height: 686px; overflow: hidden; background: var(--paper); }
  .card {
    position: relative;
    width: 1200px;
    height: 686px;
    background: var(--paper);
    font-family: "Roboto", Arial, sans-serif;
    color: var(--text);
  }
  .brand {
    position: absolute;
    left: 30px;
    top: 180px;
    width: 500px;
    display: flex;
    align-items: center;
    justify-content: center;
    gap: 18px;
  }
  .brand__square {
    width: 40px;
    height: 40px;
    background: var(--navy);
    flex: none;
  }
  .brand__name {
    font-family: "Roboto", Arial, sans-serif;
    font-weight: 400;
    font-size: 42px;
    line-height: 1;
    color: var(--ink);
    white-space: nowrap;
  }
  .divider {
    position: absolute;
    left: 0;
    top: 405px;
    width: 762px;
    height: 3px;
    background: var(--rule);
  }
  .person {
    position: absolute;
    left: 806px;
    top: 330px;
  }
  .person__name {
    font-family: "Arimo", Arial, sans-serif;
    font-weight: 700;
    font-size: 44px;
    line-height: 1;
    color: var(--navy);
    text-shadow: 2px 3px 3px rgba(0, 0, 0, 0.3);
    white-space: nowrap;
  }
  .person__title {
    margin-top: 10px;
    margin-left: 3px;
    font-size: 27px;
    line-height: 1;
    color: var(--ink);
  }
  .contact {
    position: absolute;
    left: 806px;
    top: 434px;
    list-style: none;
  }
  .contact__item {
    display: flex;
    align-items: flex-start;
    font-size: 19px;
    line-height: 24px;
    color: var(--text);
    margin-bottom: 6px;
  }
  .contact__item--tight { margin-bottom: 4px; }
  .contact__icon {
    width: 22px;
    height: 22px;
    margin-right: 33px;
    margin-top: 3px;
    flex: none;
    fill: var(--navy);
    filter: drop-shadow(1px 2px 1.5px rgba(0,0,0,0.3));
  }
</style>
</head>
<body>
  <main class="card">
    <div class="brand">
      <span class="brand__square"></span>
      <span class="brand__name">Quayvale Lawyers</span>
    </div>

    <div class="divider"></div>

    <section class="person">
      <h1 class="person__name">Paul Whitcombe</h1>
      <p class="person__title">Managing Partner</p>
    </section>

    <ul class="contact">
      <li class="contact__item">
        <svg class="contact__icon" viewBox="0 0 24 24" aria-hidden="true"><path d="M12 1C7.6 1 5 4.3 5 8c0 5 7 14 7 14s7-9 7-14c0-3.7-2.6-7-7-7zm0 10a3 3 0 1 1 0-6 3 3 0 0 1 0 6z"/></svg>
        <span>Level 9, 7 Ferris Lane<br>Sydney NSW 2000</span>
      </li>
      <li class="contact__item">
        <svg class="contact__icon" viewBox="0 0 24 24" aria-hidden="true"><path d="M7 1h10a2 2 0 0 1 2 2v18a2 2 0 0 1-2 2H7a2 2 0 0 1-2-2V3a2 2 0 0 1 2-2zm0 3v14h10V4H7zm5 15.5a1 1 0 1 0 0 2 1 1 0 0 0 0-2z"/></svg>
        <span>02 9364 2710<br>02 8472 3159</span>
      </li>
      <li class="contact__item contact__item--tight">
        <svg class="contact__icon" viewBox="0 0 24 24" aria-hidden="true"><path d="M2 10l10-7 10 7v11H2V10zm3 1.2l7 4.8 7-4.8V10l-7-4.8L5 10v1.2z"/></svg>
        <span>paul@qvlegal.com.au</span>
      </li>
      <li class="contact__item">
        <svg class="contact__icon" viewBox="0 0 24 24" aria-hidden="true"><path d="M12 2a10 10 0 1 0 0 20 10 10 0 0 0 0-20zm6.9 9h-3a15 15 0 0 0-1.3-6.2A8 8 0 0 1 18.9 11zM12 4.1c.9 1.2 1.8 3.6 1.9 6.9h-3.8c.1-3.3 1-5.7 1.9-6.9zM9.4 4.8A15 15 0 0 0 8.1 11h-3a8 8 0 0 1 4.3-6.2zM5.1 13h3a15 15 0 0 0 1.3 6.2A8 8 0 0 1 5.1 13zm6.9 6.9c-.9-1.2-1.8-3.6-1.9-6.9h3.8c-.1 3.3-1 5.7-1.9 6.9zm2.6-.7a15 15 0 0 0 1.3-6.2h3a8 8 0 0 1-4.3 6.2z"/></svg>
        <span>www.qvlegal.com.au</span>
      </li>
    </ul>
  </main>
</body>
</html>
```